K7 Electrical Services Ltd Web design

I require a web site for my new electrical contracting company. We are customer service orientated. Offering high value electrical installations, design and maintenance. Focused on custom residential and commercial upgrading. Lighting design and application are paramount in our company's services. Industry leading product use and integration are always on the forefront with our customer client services. As well as energy efficiency.

Target Market(s)

Homebuilders, General Contractors, Property management companies, clients, individuals,

Industry/Entity Type

Electric Company

Coding

Coded - Design and coding required

Number of Pages Required

3 page

Requirements
Must have
• Classic, modern, edgy but not trendy . Appeals to the masse.
• 3 page
• home page
• about page
• gallery page
• ability to contact from the webiste
Nice to have
• open to all types of designs that are relative to the construction industry.
• Black, Grey, metallic ice blue and deep purple colours from the logo.
Should not have
• anything cheesy with cartoon light bulb images.

```html
<!DOCTYPE html>
<html lang="en">
<head>
<meta charset="utf-8">
<title>K7 Electrical Services Ltd</title>
<link rel="stylesheet" href="https://fonts.googleapis.com/css2?family=Oswald:wght@300;400;500&family=Roboto:ital,wght@0,400;0,500;0,700;1,400&display=swap">
<style>
:root{
  --purple:#7c30bd;
  --purple-light:#9247d6;
  --purple-deep:#4a1a7c;
  --ink:#2b2b2b;
  --muted:#6d6d6d;
  --paper:#ffffff;
  --mist:#f3f3f3;
  --footer:#2f2f2f;
  --footer-base:#272727;
  --footer-text:#8a8a8a;
}
*{margin:0;padding:0;box-sizing:border-box}
html,body{width:1200px;height:2500px;overflow:hidden;background:var(--paper)}
body{position:relative;font-family:"Roboto",Arial,sans-serif;color:var(--ink)}
.abs{position:absolute}
h1,h2,h3{font-family:"Oswald","Arial Narrow",sans-serif;font-weight:400}

/* header */
.site-header{left:0;top:0;width:1200px;height:83px;background:var(--paper)}
.brand{left:200px;top:24px;display:flex;align-items:center;gap:8px;height:34px}
.brand-mark{width:11px;height:11px;background:var(--purple-deep)}
.brand-name{font-family:"Oswald",sans-serif;font-size:16px;font-weight:400;color:var(--purple-deep);letter-spacing:1px;text-transform:uppercase;white-space:nowrap}
.nav-link{top:33px;font-size:11.5px;font-weight:500;text-transform:uppercase;color:var(--ink);text-decoration:none;white-space:nowrap;display:flex;align-items:center;gap:8px}
.nav-link.is-active{color:var(--purple)}
.header-phone{left:876px;top:30px;display:flex;align-items:center;gap:10px;font-size:15px;font-weight:700}

/* hero */
.hero{left:0;top:83px;width:1200px;height:534px;overflow:hidden}
.hero-shade{left:0;top:0;width:600px;height:534px;background:linear-gradient(135deg,#4a4a4a,#2e2e2e 60%,#3a3a3a)}
.hero-photo{left:600px;top:0;width:600px;height:534px;background:linear-gradient(160deg,#e9e6e1,#cfcac3 45%,#8a95b0 70%,#d8d4cf)}
.hero-title{left:200px;top:145px;font-size:50px;line-height:60px;color:#fff;font-weight:400;white-space:nowrap}
.hero-text{left:200px;top:283px;width:370px;font-size:12.5px;line-height:20px;color:#eee}
.btn-solid{left:200px;top:375px;width:125px;height:42px;background:var(--purple);color:#fff;font-size:12px;font-weight:700;text-transform:uppercase;display:flex;align-items:center;justify-content:center;box-shadow:0 3px 0 var(--purple-deep)}
.slider-dots{display:flex;gap:9px}
.slider-dots span{width:17px;height:2px;background:#ddd}

/* intro + contact */
.intro{left:0;top:617px;width:600px;height:280px;background:var(--mist)}
.intro-photo{left:462px;top:13px;width:130px;height:267px;background:linear-gradient(180deg,#e9cfb8 0 22%,#3b5fa0 22% 62%,#b9a68c 62%)}
.intro-quote{left:200px;top:65px;width:258px;font-size:17px;line-height:25px;font-style:italic;color:var(--ink);z-index:1}
.intro-text{left:200px;top:129px;width:232px;font-size:11.5px;line-height:19px;color:#444}
.btn-outline{left:200px;top:188px;width:103px;height:38px;border:1px solid var(--purple);color:var(--purple);font-size:10.5px;font-weight:500;text-transform:uppercase;display:flex;align-items:center;justify-content:center}
.contact-panel{left:600px;top:617px;width:600px;height:280px;background:var(--purple)}
.contact-title{left:53px;top:43px;font-size:28px;color:#fff}
.field{height:35px;width:140px;background:var(--purple-light);color:#fff;font-size:11px;padding:12px 0 0 15px}
.submit{left:53px;top:191px;width:290px;height:37px;background:#fff;color:var(--purple-deep);font-size:11px;font-weight:500;text-transform:uppercase;display:flex;align-items:center;justify-content:center}

/* about */
.section-title{font-size:28px;color:var(--purple-deep);white-space:nowrap}
.title-rule{height:1px;background:var(--purple-deep)}
.about-text{left:200px;top:1008px;width:775px;font-size:12.5px;line-height:21px;color:#333}
.service-card{top:1075px;width:240px;height:120px;border:1px solid #cfc4dc;background:#fff;box-shadow:2px 3px 0 #e3e3e3}
.service-card h3{position:absolute;left:13px;top:16px;font-family:"Roboto",sans-serif;font-size:12px;font-weight:500;color:#111}
.service-card p{position:absolute;left:13px;top:40px;width:155px;font-size:10.5px;line-height:16px;color:#555}
.service-card .more{position:absolute;left:13px;top:91px;font-size:10.5px;font-weight:500;color:var(--purple-deep)}
.service-card svg{position:absolute;right:0;top:0}

/* testimonials */
.tools-photo{left:0;top:1265px;width:600px;height:467px;background:linear-gradient(150deg,#f1f1ef,#dcdcd8 40%,#e8743a 62%,#e9e9e6 75%,#cfcfcb)}
.clients{left:600px;top:1265px;width:600px;height:467px;background:linear-gradient(135deg,#4c4c4c,#353535 55%,#5a4a40)}
.clients-title{left:0;top:64px;width:404px;text-align:center;font-size:28px;color:#fff}
.clients-sub{left:75px;top:112px;width:254px;text-align:center;font-size:11px;line-height:18px;font-weight:700;color:#fff;text-transform:uppercase}
.clients-quote{left:42px;top:163px;width:342px;text-align:center;font-size:11px;line-height:20px;font-style:italic;color:#ddd}
.clients-quote-mark{left:15px;top:158px;font-family:Georgia,serif;font-size:28px;color:#fff;font-weight:700}
.avatar{left:167px;top:252px;width:70px;height:70px;border-radius:50%;background:linear-gradient(180deg,#d9d4cf,#6f6a6a);border:2px solid #fff}
.clients-name{left:0;top:338px;width:404px;text-align:center;font-size:11px;color:#ccc}

/* projects */
.projects-text{left:200px;top:1837px;font-size:12px;color:#333}
.tile{top:1883px;height:218px}
.tile-overlay{left:400px;top:1883px;width:200px;height:218px;background:var(--purple);color:#fff;text-align:center}
.tile-overlay h3{font-family:"Roboto",sans-serif;font-size:15px;font-weight:500;line-height:21px;margin:35px 20px 12px}
.tile-overlay p{font-size:10.5px;line-height:17px;margin:0 22px}
.arrows{left:575px;top:2126px;display:flex;gap:2px}
.arrows span{width:24px;height:24px;background:#ddd;display:flex;align-items:center;justify-content:center}

/* footer */
.site-footer{left:0;top:2212px;width:1200px;height:233px;background:var(--footer)}
.footer-base{left:0;top:2445px;width:1200px;height:55px;background:var(--footer-base);border-top:1px solid #3d3d3d}
.footer-head{font-family:"Roboto",sans-serif;font-size:12.5px;font-weight:700;color:#fff;text-transform:uppercase}
.footer-note{font-size:11px;color:var(--footer-text)}
.footer-links{list-style:none;font-size:11px;color:var(--footer-text);line-height:24px}
.email-field{left:200px;top:2340px;width:247px;height:37px;background:#fff;font-size:11px;color:#555;padding:12px 0 0 12px}
.contact-row{display:flex;align-items:flex-start;gap:14px;font-size:11px;color:var(--footer-text);line-height:16px}
.social{left:880px;top:2462px;display:flex;gap:10px}
.social span{width:20px;height:20px;background:#555;border:1px solid #777}
</style>
</head>
<body>

<header class="site-header abs">
  <div class="brand abs"><span class="brand-mark"></span><span class="brand-name">K7 Electrical Services</span></div>
  <nav>
    <a class="nav-link is-active abs" style="left:447px;top:31px" href="#"><svg width="18" height="15" viewBox="0 0 18 15"><path d="M9 1 1 8h2.5v6h4v-4h3v4h4V8H17z" fill="#7c30bd"/></svg>Home</a>
    <a class="nav-link abs" style="left:553px" href="#">About Us</a>
    <a class="nav-link abs" style="left:648px" href="#">Gallery</a>
    <a class="nav-link abs" style="left:738px" href="#">Contact Us</a>
  </nav>
  <div class="header-phone abs">
    <svg width="18" height="18" viewBox="0 0 18 18"><path d="M4 1h3l1.5 4-2 1.3a9 9 0 0 0 5.2 5.2L13 9.5l4 1.5v3a2 2 0 0 1-2 2A14 14 0 0 1 2 3a2 2 0 0 1 2-2z" fill="#7c30bd"/></svg>
    <span>+1555010274</span>
  </div>
</header>

<section class="hero abs">
  <div class="hero-shade abs" role="img" aria-label="Kitchen with open electrical panel, darkened"></div>
  <div class="hero-photo abs" role="img" aria-label="Electrician in blue overalls working on wiring in a kitchen"></div>
  <h1 class="hero-title abs">Welcome to Electrical<br>Services</h1>
  <p class="hero-text abs">Lorem Ipsum is simply dummy text of the printing and typesetting industry. Lorem Ipsum has been the industry's standard dummy text ever since the 1500s, lorem ipsum is text...</p>
  <a class="btn-solid abs">Learn More</a>
  <div class="slider-dots abs" style="left:200px;top:458px"><span></span><span></span><span></span></div>
</section>

<section class="intro abs">
  <div class="intro-photo abs" role="img" aria-label="Smiling electrician with tool belt giving an okay sign"></div>
  <p class="intro-quote abs">" Lorem Ipsum is simply dummy text of the printing "</p>
  <p class="intro-text abs">Lorem Ipsum is simply dummy text oftprint-ing and typesetting industry...</p>
  <a class="btn-outline abs">Learn More &rarr;</a>
</section>

<section class="contact-panel abs">
  <h2 class="contact-title abs">Contact Us</h2>
  <div class="field abs" style="left:53px;top:95px">Name :</div>
  <div class="field abs" style="left:205px;top:95px">Phone :</div>
  <div class="field abs" style="left:53px;top:141px">E-mail :</div>
  <div class="field abs" style="left:205px;top:141px">Message :</div>
  <div class="submit abs">Submit Information</div>
</section>

<h2 class="section-title abs" style="left:200px;top:950px">About Us</h2>
<div class="title-rule abs" style="left:200px;top:991px;width:130px"></div>
<p class="about-text abs">Lorem Ipsum is simply dummy text of the printing and typesetting industry. Lorem Ipsum has been the industry's standard dummy text ever since the 1500s, when an unknown printer took a galley of type and scrambled it to make a type specimen book.</p>

<article class="service-card abs" style="left:200px">
  <svg width="68" height="118" viewBox="0 0 68 118"><path d="M20 0h48v118H20L0 59z" fill="#7c30bd"/><circle cx="30" cy="59" r="14" fill="none" stroke="#fff" stroke-width="3"/><path d="M25 55h9M25 63h9M34 52v14" stroke="#fff" stroke-width="3"/></svg>
  <h3>Lorem Ipsum is a Text</h3>
  <p>Lorem Ipsum is simply dummy text of theprinting and typeset-ting industry.</p>
  <span class="more">Learn More &rarr;</span>
</article>
<article class="service-card abs" style="left:480px">
  <svg width="68" height="118" viewBox="0 0 68 118"><path d="M20 0h48v118H20L0 59z" fill="#7c30bd"/><circle cx="30" cy="59" r="14" fill="none" stroke="#fff" stroke-width="3"/><path d="M25 55h9M25 63h9M34 52v14" stroke="#fff" stroke-width="3"/></svg>
  <h3>Lorem Ipsum is a Text</h3>
  <p>Lorem Ipsum is simply dummy text of theprinting and typeset-ting industry.</p>
  <span class="more">Learn More &rarr;</span>
</article>
<article class="service-card abs" style="left:760px">
  <svg width="68" height="118" viewBox="0 0 68 118"><path d="M20 0h48v118H20L0 59z" fill="#7c30bd"/><circle cx="30" cy="59" r="14" fill="none" stroke="#fff" stroke-width="3"/><path d="M25 55h9M25 63h9M34 52v14" stroke="#fff" stroke-width="3"/></svg>
  <h3>Lorem Ipsum is a Text</h3>
  <p>Lorem Ipsum is simply dummy text of theprinting and typeset-ting industry.</p>
  <span class="more">Learn More &rarr;</span>
</article>

<div class="tools-photo abs" role="img" aria-label="Multimeter with red and black probes on electrical plans"></div>
<section class="clients abs" aria-label="Testimonials">
  <h2 class="clients-title abs">Clients Say</h2>
  <p class="clients-sub abs">Lorem Ipsum is simply dummy text of the printing and typesetting..</p>
  <span class="clients-quote-mark abs">&ldquo;</span>
  <p class="clients-quote abs">Lorem Ipsum is simply dummy text of the printing and typesetting indus-try.Lorem Ipsum has been the industry's standard dummy text ever since the 1500s, when an unknown printer took a galley of type..</p>
  <div class="avatar abs" role="img" aria-label="Client portrait"></div>
  <p class="clients-name abs">Clara Whitfield, 19 Feb-2018</p>
  <div class="slider-dots abs" style="left:170px;top:393px"><span></span><span></span><span></span></div>
</section>

<h2 class="section-title abs" style="left:200px;top:1780px">Our Completed Projects</h2>
<div class="title-rule abs" style="left:200px;top:1824px;width:295px"></div>
<p class="projects-text abs">Lorem Ipsum is simply dummy text of the printing and typesetting industry.</p>
<div class="tile abs" style="left:200px;width:200px;background:linear-gradient(160deg,#e0c44a 0 15%,#b9c3cf 15% 60%,#5a6070)" role="img" aria-label="Electrician in hard hat wiring a control panel"></div>
<div class="tile-overlay abs">
  <h3>Lorem Ipsum is simply dummy text</h3>
  <p>Lorem Ipsum is simply dummy text of the printing and typeset-ting text industry.</p>
  <svg class="abs" style="left:83px;top:143px" width="34" height="34" viewBox="0 0 34 34"><path d="M17 1l14 8v16l-14 8-14-8V9z" fill="#fff"/><circle cx="16" cy="16" r="5" fill="none" stroke="#7c30bd" stroke-width="2"/><path d="M20 20l4 4" stroke="#7c30bd" stroke-width="2"/></svg>
</div>
<div class="tile abs" style="left:600px;width:200px;background:linear-gradient(160deg,#eef0f2 0 30%,#2d4f9a 30% 75%,#c9ced6)" role="img" aria-label="Electrician in white hard hat working on a fuse box"></div>
<div class="tile abs" style="left:800px;width:200px;background:linear-gradient(160deg,#f0b43a 0 20%,#c8c9c4 20% 60%,#6e7a62)" role="img" aria-label="Two engineers in hard hats reviewing plans"></div>
<div class="arrows abs">
  <span><svg width="12" height="8" viewBox="0 0 12 8"><path d="M11 4H1M4 1 1 4l3 3" stroke="#333" fill="none" stroke-width="1.5"/></svg></span>
  <span><svg width="12" height="8" viewBox="0 0 12 8"><path d="M1 4h10M8 1l3 3-3 3" stroke="#333" fill="none" stroke-width="1.5"/></svg></span>
</div>

<footer class="site-footer abs">
  <h3 class="footer-head abs" style="left:200px;top:58px">Stay In Touch</h3>
  <p class="footer-note abs" style="left:200px;top:97px">Sign up here to receive interesting updates</p>
  <h3 class="footer-head abs" style="left:517px;top:58px">Quick Links</h3>
  <ul class="footer-links abs" style="left:517px;top:91px"><li>Home</li><li>About Us</li><li>Gallery</li><li>Contact Us</li></ul>
  <ul class="footer-links abs" style="left:667px;top:91px"><li>Help</li><li>Account</li><li>Privacy Policy</li><li>Terms and Condition</li></ul>
  <h3 class="footer-head abs" style="left:845px;top:58px">Contact Us</h3>
  <div class="contact-row abs" style="left:847px;top:97px"><svg width="14" height="14" viewBox="0 0 18 18"><path d="M4 1h3l1.5 4-2 1.3a9 9 0 0 0 5.2 5.2L13 9.5l4 1.5v3a2 2 0 0 1-2 2A14 14 0 0 1 2 3a2 2 0 0 1 2-2z" fill="#9a9a9a"/></svg><span>+1555010274</span></div>
  <div class="contact-row abs" style="left:847px;top:134px"><svg width="14" height="16" viewBox="0 0 14 18"><path d="M7 1a6 6 0 0 1 6 6c0 4-6 10-6 10S1 11 1 7a6 6 0 0 1 6-6z" fill="#9a9a9a"/><circle cx="7" cy="7" r="2" fill="#2f2f2f"/></svg><span>Lorem Ipsum is simply<br>of the printing</span></div>
  <div class="contact-row abs" style="left:847px;top:184px"><svg width="16" height="12" viewBox="0 0 16 12"><rect x="0.5" y="0.5" width="15" height="11" fill="#9a9a9a"/><path d="M1 1l7 6 7-6" stroke="#2f2f2f" fill="none"/></svg><span>info@k7electrical.com</span></div>
</footer>
<div class="email-field abs">Email Address
  <svg class="abs" style="left:203px;top:11px" width="20" height="16" viewBox="0 0 20 16"><path d="M1 8 19 1l-4 14-5-5z" fill="#222"/></svg>
</div>

<div class="footer-base abs">
  <p class="footer-note abs" style="left:200px;top:20px">&copy; Copyright 2018 K7 electrical.&nbsp; All Rights Reserved.</p>
</div>
<div class="social abs"><span></span><span></span><span></span><span></span></div>

</body>
</html>
```